Looking for a modern, Professional business card design

We have a simple business card, but are looking for a more modern, professional look. A sample of the basic card is attached as well as the logo. We would also like to add that we offer:
Struggling with your finances?
- Learn to become debt free
- Discover the power of cash
- Control your money instead of it controlling you
Let us help you achieve a new level of financial freedom!
Also, we would like to have a "SPECIAL OFFER!: FREE 30 minute consultation"
Financial Planning

```html
<!DOCTYPE html>
<html lang="en">
<head>
<meta charset="utf-8">
<title>Summit Money Coaching – Business Card</title>
<link href="https://fonts.googleapis.com/css2?family=Open+Sans:ital,wght@0,400;0,600;0,700;0,800;1,400&display=swap" rel="stylesheet">
<style>
  :root {
    --page-bg: #ecebe6;
    --card-white: #ffffff;
    --card-shade: #e6e6e6;
    --green-dark: #2f8f3a;
    --green-mid: #5cb536;
    --green-light: #b5dc4a;
    --ink: #1d1d1d;
    --ink-soft: #333333;
    --muted: #6b6b6b;
  }
  * { box-sizing: border-box; margin: 0; padding: 0; }
  html, body { width: 1200px; height: 843px; overflow: hidden; }
  body {
    background: var(--page-bg);
    font-family: "Open Sans", Arial, sans-serif;
    display: flex;
    align-items: center;
    justify-content: center;
    gap: 40px;
  }
  .card {
    position: relative;
    width: 540px;
    height: 309px;
    border-radius: 18px;
    overflow: hidden;
    box-shadow: 0 10px 26px rgba(0,0,0,0.25);
    background: linear-gradient(180deg, var(--card-white) 60%, var(--card-shade) 100%);
  }

  /* Back of card */
  .card-back .pitch {
    position: absolute;
    left: 30px;
    top: 34px;
    width: 470px;
    color: var(--ink-soft);
  }
  .pitch-heading {
    color: var(--green-dark);
    font-weight: 700;
    font-size: 15px;
    letter-spacing: 0.2px;
  }
  .benefits {
    list-style: none;
    margin-top: 4px;
  }
  .benefits li {
    position: relative;
    padding-left: 16px;
    font-style: italic;
    font-size: 14px;
    line-height: 19px;
  }
  .benefits li::before {
    content: "";
    position: absolute;
    left: 2px;
    top: 7px;
    width: 6px;
    height: 6px;
    border-radius: 50%;
    background: var(--green-mid);
  }
  .pitch-closing {
    font-style: italic;
    font-size: 14px;
    margin-top: 3px;
  }
  .offer-label {
    margin-top: 14px;
    color: var(--green-dark);
    font-weight: 800;
    font-size: 17px;
    line-height: 20px;
  }
  .offer-detail {
    color: var(--ink);
    font-weight: 700;
    font-size: 13px;
  }
  .back-brand {
    position: absolute;
    left: 30px;
    right: 30px;
    bottom: 30px;
    font-weight: 800;
    font-size: 27px;
    line-height: 1;
    color: var(--ink);
    letter-spacing: 0.5px;
    text-transform: uppercase;
    white-space: nowrap;
  }

  /* Front of card */
  .card-front .front-art {
    position: absolute;
    inset: 0;
    width: 100%;
    height: 100%;
  }
  .holder {
    position: absolute;
    left: 24px;
    top: 22px;
    color: var(--card-white);
  }
  .holder-name { font-size: 20px; font-weight: 600; line-height: 24px; }
  .holder-role { font-size: 15px; font-weight: 400; }
  .contact {
    position: absolute;
    left: 24px;
    bottom: 24px;
    color: var(--card-white);
    font-size: 13.5px;
    line-height: 20px;
  }
  .front-brand {
    position: absolute;
    left: 362px;
    right: 14px;
    top: 122px;
  }
  .front-brand .brand-row {
    display: flex;
    align-items: center;
    gap: 8px;
  }
  .brand-dot {
    width: 14px;
    height: 14px;
    border-radius: 50%;
    background: var(--green-mid);
    flex: none;
  }
  .brand-name {
    font-weight: 800;
    font-size: 16px;
    line-height: 19px;
    color: var(--ink);
    text-transform: uppercase;
  }
  .brand-tagline {
    margin-top: 6px;
    font-size: 8.5px;
    line-height: 12px;
    color: var(--muted);
  }
</style>
</head>
<body>

  <section class="card card-back" aria-label="Business card back">
    <div class="pitch">
      <p class="pitch-heading">STRUGGLING WITH YOUR FINANCES?</p>
      <ul class="benefits">
        <li>Learn to become debt free</li>
        <li>Discover the power of cash</li>
        <li>Control your money instead of it controlling you</li>
      </ul>
      <p class="pitch-closing">Let us help you achieve a new level of financial freedom!</p>
      <p class="offer-label">SPECIAL OFFER!</p>
      <p class="offer-detail">FREE 30 minute consultation</p>
    </div>
    <p class="back-brand">Summit Money Coaching</p>
  </section>

  <section class="card card-front" aria-label="Business card front">
    <svg class="front-art" viewBox="0 0 540 309" preserveAspectRatio="none" aria-hidden="true">
      <defs>
        <radialGradient id="greenPanel" cx="0.55" cy="0.35" r="0.75">
          <stop offset="0" stop-color="#b9e04e"/>
          <stop offset="0.5" stop-color="#6fbe3a"/>
          <stop offset="1" stop-color="#2f8f3a"/>
        </radialGradient>
        <linearGradient id="lightArc" x1="0" y1="0" x2="0" y2="1">
          <stop offset="0" stop-color="#c9e86a"/>
          <stop offset="1" stop-color="#6fbe3a"/>
        </linearGradient>
      </defs>
      <path d="M0 0 H400 C 300 50, 270 200, 330 309 H0 Z" fill="url(#greenPanel)"/>
      <path d="M400 0 H430 C 325 55, 296 200, 352 309 H330 C 270 200, 300 50, 400 0 Z" fill="url(#lightArc)"/>
      <path d="M430 0 H444 C 340 58, 312 200, 366 309 H352 C 296 200, 325 55, 430 0 Z" fill="#1d1d1d"/>
    </svg>

    <div class="holder">
      <p class="holder-name">Daniel R. Hayes</p>
      <p class="holder-role">Personal Financial Coach</p>
    </div>

    <div class="contact">
      <p>(555) 014-2837</p>
      <p>daniel@steadymoneypath.com</p>
      <p>www.steadymoneypath.com</p>
    </div>

    <div class="front-brand">
      <div class="brand-row">
        <span class="brand-dot"></span>
        <span class="brand-name">Summit Money Coaching</span>
      </div>
      <p class="brand-tagline">Achieve a new level of personal freedom</p>
    </div>
  </section>

</body>
</html>
```